PixelMarrow Inc. Website & iPhone Apps Landing Pages

We need a web site design for our company. We develop software and do various consultant projects for our clients. Our products focus on the mobile platform, mainly the iPhone (business, games, social, etc.). We want to communicate that our software is simple and good as candy. The web pages should be fun to look at not loosing seriousness and credibility. Web 2.0 style and 960 grid system a must. We are opened to any overall site colour scheme suggestions (look at the sites we like below).

Must haves:
- Our logo should be seen on the site and look great on it :-) (preview attached below)
- Main home page and app landing page.
- Section links/tabs on the home page (home,apps,support,blog,contact,about)
- No text in images
- Style sheet

Looks we like:
- http://k7q3vxp9lrtwz.examplecdn.net/441_Site_Mock/final_large.jpg
- http://k7q3vxp9lrtwz.examplecdn.net/Deluxe_71_Drawn_Phone_Landing_Page/final.jpg
- http://grenmoor.com/
- http://lumbrel.ca/
- http://fairtwig.com/

Industry/Entity Type

Business

Requirements
Must have
• - Company logo should look great on pages.
• - Main home page and app landing page.
• - Section links/tabs on the home page (home,apps,support,blog,contact,about)
• - Web 2.0 style.
• - 960 grid system (12 col, 16 col).
• - Sliced ann optmized
• - Exported in all major formats (psd,ai,eps,png,jpeg,etc)
• - Style sheet
Should not have
• - Text in images

```html
<!DOCTYPE html>
<html lang="en">
<head>
<meta charset="utf-8">
<title>PixelMarrow – Apps</title>
<link href="https://fonts.googleapis.com/css2?family=Poppins:wght@500;600&family=Open+Sans:wght@400;600;700&display=swap" rel="stylesheet">
<style>
  :root {
    --bar-dark: #2a2a2a;
    --bar-line: #353535;
    --social-blue: #a3c5f7;
    --hero-top: #ffffff;
    --hero-bottom: #c2d7fb;
    --candy-red: #d7141f;
    --ink: #1e1610;
    --body-text: #3c3c3c;
    --link-blue: #2a4f9a;
    --pale: #eeeeee;
    --white: #ffffff;
  }
  * { margin: 0; padding: 0; box-sizing: border-box; }
  html, body { width: 1200px; height: 950px; overflow: hidden; }
  body { position: relative; background: var(--white); font-family: "Open Sans", Arial, sans-serif; color: var(--body-text); }

  .site-header { position: absolute; left: 0; top: 0; width: 1200px; height: 67px;
    background: repeating-linear-gradient(135deg, var(--bar-dark) 0 6px, var(--bar-line) 6px 8px); }
  .brand { position: absolute; left: 130px; top: 12px; font-family: "Poppins", sans-serif; font-weight: 600;
    font-size: 30px; color: var(--white); letter-spacing: 0.5px; }
  .main-nav { position: absolute; top: 22px; left: 620px; display: flex; gap: 0; font-family: "Poppins", sans-serif;
    font-weight: 500; font-size: 15px; color: var(--white); }
  .main-nav a { color: inherit; text-decoration: none; margin-right: 27px; }
  .main-nav .current::before { content: "{ "; color: var(--candy-red); }
  .main-nav .current::after { content: " }"; color: var(--candy-red); }

  .social-bar { position: absolute; left: 0; top: 68px; width: 1200px; height: 43px; background: var(--social-blue);
    border-top: 1px solid #c8dcfa; }
  .follow { position: absolute; top: 12px; display: flex; align-items: center; gap: 10px; color: var(--white);
    font-size: 14px; }
  .follow .dot { width: 32px; height: 32px; border-radius: 50%; background: #2f5aa8; margin-top: -4px; }
  .follow.chirp .dot { background: #2aa7dc; }

  .hero { position: absolute; left: 0; top: 111px; width: 1200px; height: 364px;
    background: linear-gradient(var(--hero-top), var(--hero-bottom)); }
  .hero-art { position: absolute; left: 125px; top: 20px; width: 530px; height: 350px; }
  .featured { position: absolute; left: 690px; top: 40px; }
  .featured h1 { font-family: "Poppins", sans-serif; font-weight: 600; font-size: 44px; color: var(--ink);
    letter-spacing: -1px; line-height: 1; }
  .app-name { margin-top: 8px; font-size: 18px; color: var(--candy-red); text-transform: uppercase; }
  .label { font-size: 14px; color: #111; font-weight: 600; margin-top: 8px; }
  .overview { font-size: 13px; line-height: 24px; margin-top: 4px; letter-spacing: 0.3px; }
  .client { font-size: 16px; color: var(--candy-red); }
  .learn-more { display: block; margin-top: 15px; margin-left: -4px; width: 166px; height: 41px; border-radius: 6px;
    background: linear-gradient(#e42a2f, #b5101a); border: 1px solid #8f0d12; color: var(--white);
    font-family: "Poppins", sans-serif; font-weight: 600; font-size: 16px; text-align: center; line-height: 39px;
    text-decoration: none; letter-spacing: 0.5px; }

  .lower { position: absolute; left: 0; top: 475px; width: 1200px; height: 397px;
    background: linear-gradient(#ebebeb, var(--white) 120px); }
  .more-title { position: absolute; left: 128px; top: 36px; font-family: "Poppins", sans-serif; font-weight: 600;
    font-size: 27px; color: var(--ink); letter-spacing: -0.5px; }
  .app-card { position: absolute; top: 96px; width: 290px; }
  .app-card .app-name { margin-top: 0; }
  .app-card .client { margin-top: 2px; }

  .sidebar { position: absolute; left: 769px; top: 14px; width: 280px; }
  .blog-heading { display: flex; align-items: center; gap: 44px; }
  .post-title { margin-top: 10px; font-size: 18px; color: var(--candy-red); }
  .post-title time { font-size: 11px; color: #222; font-weight: 700; margin-left: 8px; }
  .chirp-box { margin-top: 20px; width: 117px; height: 52px; background: linear-gradient(#a6c6ef, #7ea6dd);
    color: var(--white); font-weight: 700; font-size: 16px; text-align: center; line-height: 52px; }
  .chirp-post { margin-top: 22px; font-size: 13px; line-height: 24px; }
  .chirp-post a { color: var(--link-blue); text-decoration: none; }

  .site-footer { position: absolute; left: 0; top: 872px; width: 1200px; height: 78px;
    background: repeating-linear-gradient(135deg, var(--bar-dark) 0 6px, var(--bar-line) 6px 8px); color: var(--white); }
  .footer-nav a { position: absolute; top: 15px; color: var(--white); text-decoration: none; font-size: 13px;
    font-weight: 600; }
  .copyright { position: absolute; top: 44px; left: 0; width: 1247px; text-align: center; font-size: 12px; }
</style>
</head>
<body>
  <header class="site-header">
    <div class="brand">pixelmarrow</div>
    <nav class="main-nav">
      <a href="#">home</a><a href="#" class="current">apps</a><a href="#">support</a><a href="#">blog</a><a href="#">contact</a><a href="#">about</a>
    </nav>
  </header>

  <div class="social-bar">
    <a class="follow" style="left:620px">Follow us on Friendloop <span class="dot"></span></a>
    <a class="follow chirp" style="left:858px">Follow us on Chirpline <span class="dot"></span></a>
  </div>

  <section class="hero">
    <svg class="hero-art" role="img" aria-label="Three phones showing a red and white candy swirl, with a peppermint candy and a script banner reading Our Sweetened Apps" viewBox="0 0 530 350">
      <defs>
        <linearGradient id="heroArtTone" x1="0" y1="0" x2="0" y2="1">
          <stop offset="0" stop-color="#e03a3f"/>
          <stop offset="1" stop-color="#c4d6f5"/>
        </linearGradient>
      </defs>
      <rect width="530" height="350" rx="14" fill="url(#heroArtTone)" opacity="0.35"/>
    </svg>
    <div class="featured">
      <h1>Featured App</h1>
      <div class="app-name">The Candy Shop</div>
      <div class="label">Project Overview</div>
      <p class="overview">Our products focus on the mobile platform.<br>Whatever your project {business, games, social, etc.}<br>we will make your app as sweet as candy.</p>
      <div class="label" style="font-weight:400;margin-top:14px">Client</div>
      <div class="client">My Sweet Shop</div>
      <a class="learn-more" href="#">LEARN MORE</a>
    </div>
  </section>

  <section class="lower">
    <h2 class="more-title">More Apps</h2>
    <article class="app-card" style="left:130px">
      <div class="app-name">App Title</div>
      <div class="label">Project Overview</div>
      <p class="overview">Lorem ipsum dolor sit amet, consectetur<br>adipiscing elit. Quisque non ipsum enim.<br>Nunc rhoncus pretium fringilla. Nulla id ...</p>
      <div class="label" style="font-weight:400;margin-top:12px">Client</div>
      <div class="client">The Client</div>
    </article>
    <article class="app-card" style="left:454px;top:94px">
      <div class="app-name">App Title</div>
      <div class="label">Project Overview</div>
      <p class="overview">Lorem ipsum dolor sit amet, consectetur<br>adipiscing elit. Quisque non ipsum enim.<br>Nunc rhoncus pretium fringilla. Nulla id ...</p>
      <div class="label" style="font-weight:400;margin-top:12px">Client</div>
      <div class="client">The Client</div>
    </article>

    <aside class="sidebar">
      <div class="blog-heading">
        <svg role="img" aria-label="Script lettering reading Latest Blog Post" width="142" height="30" viewBox="0 0 142 30">
          <rect width="142" height="30" rx="6" fill="#d7141f"/>
        </svg>
        <svg width="52" height="38" viewBox="0 0 52 38" aria-hidden="true">
          <ellipse cx="18" cy="17" rx="17" ry="12" fill="#a9c7f4"/>
          <path d="M10 26 L6 36 L18 28 Z" fill="#a9c7f4"/>
          <ellipse cx="34" cy="13" rx="16" ry="11" fill="#8db4ef"/>
          <path d="M40 22 L46 30 L36 23 Z" fill="#8db4ef"/>
        </svg>
      </div>
      <div class="post-title">Latest Blog Title <time>10.26.2010</time></div>
      <p class="overview">Lorem ipsum dolor sit amet, consectetur<br>adipiscing elit. Quisque non ipsum enim.<br>Nunc rhoncus pretium fringilla. Nulla id ...</p>
      <div class="chirp-box">Chirpline</div>
      <p class="chirp-post"><a href="#">About 1 day ago</a>&nbsp; What a great client<br>&nbsp;we have to work with, check them out ...<br><a href="#">link to the client</a></p>
    </aside>
  </section>

  <footer class="site-footer">
    <nav class="footer-nav">
      <a href="#" style="left:279px">HOME</a>
      <a href="#" style="left:391px">APPS</a>
      <a href="#" style="left:495px">SUPPORT</a>
      <a href="#" style="left:614px">BLOG</a>
      <a href="#" style="left:738px">CONTACT</a>
      <a href="#" style="left:888px">ABOUT</a>
    </nav>
    <p class="copyright">Copyright 2010 PixelMarrow. All Rights Reserved</p>
  </footer>
</body>
</html>
```